Bref créative
Harbor Keys Stationary
Fast Settlements
Professional
RoberT Dunmore
Managing Member
4872 J St NW Suite 500
Washington, DC
rpdunmore@harborkeys-example.net
www.harborkeys-example.net
Business License # 758264139207
Cash Buyer, Fast Closing.
Residential and Commercial
We are a Nation Wide Buyer.
will upload ai file shortly
vector logo file

```html
<!DOCTYPE html>
<html lang="en">
<head>
<meta charset="utf-8">
<title>Harbor Keys – Business Card</title>
<link href="https://fonts.googleapis.com/css2?family=Russo+One&family=Montserrat:wght@400;500;600&display=swap" rel="stylesheet">
<style>
  :root {
    --backdrop: #e9e7e3;
    --card: #fbfbfa;
    --green: #1f8f3c;
    --green-dark: #146a2b;
    --ink: #2b2b2b;
    --muted: #555555;
    --black-band: #1c1c1c;
  }
  * { margin: 0; padding: 0; box-sizing: border-box; }
  html, body {
    width: 1200px; height: 914px; overflow: hidden;
    background: var(--backdrop);
  }
  .card {
    position: absolute; left: 100px; top: 171px;
    width: 1000px; height: 572px;
    background: var(--card);
    box-shadow: 0 6px 24px rgba(0,0,0,.12);
    overflow: hidden;
    font-family: "Montserrat", sans-serif;
    color: var(--ink);
  }
  .brand {
    position: absolute; left: 0; right: 0; top: 150px;
    display: flex; justify-content: center; align-items: center; gap: 18px;
  }
  .brand-mark {
    width: 46px; height: 46px; background: var(--green-dark);
  }
  .brand-name {
    font-family: "Russo One", sans-serif;
    font-size: 64px; letter-spacing: 3px;
    color: var(--green-dark); text-transform: uppercase;
    line-height: 1;
  }
  .details {
    position: absolute; left: 0; right: 0; top: 300px;
    display: flex; justify-content: center;
  }
  .person {
    width: 330px; padding-right: 26px; text-align: right;
    border-right: 2px solid #9a9a9a;
    letter-spacing: 1.5px; text-transform: uppercase;
  }
  .person-name { color: var(--green); font-weight: 600; font-size: 17px; }
  .person-title { color: var(--muted); font-size: 13px; margin-top: 4px; }
  .person-address { font-size: 14px; margin-top: 22px; line-height: 1.7; }
  .contacts { list-style: none; padding-left: 22px; }
  .contacts li {
    display: flex; align-items: center; gap: 10px;
    font-size: 13.5px; letter-spacing: 1.2px; line-height: 1; margin-bottom: 8px;
  }
  .contacts svg { width: 18px; height: 18px; flex: none; }
  .bands { position: absolute; left: 0; bottom: 0; width: 1000px; height: 110px; }
</style>
</head>
<body>
  <div class="card">
    <div class="brand">
      <span class="brand-mark"></span>
      <span class="brand-name">Harbor Keys</span>
    </div>

    <div class="details">
      <div class="person">
        <p class="person-name">RoberT Dunmore</p>
        <p class="person-title">Managing Member</p>
        <p class="person-address">4872 J St NW Suite 500<br>Washington, DC 20005</p>
      </div>
      <ul class="contacts">
        <li>
          <svg viewBox="0 0 18 18"><circle cx="9" cy="9" r="9" fill="var(--green)"/><path d="M6 5l2 2-1 1.3c.7 1.3 1.5 2.1 2.7 2.7L11 10l2 2-1.3 1.3C9 13 5 9 4.7 6.3z" fill="#fff"/></svg>
          1-800-555-0142
        </li>
        <li>
          <svg viewBox="0 0 18 18"><circle cx="9" cy="9" r="9" fill="var(--green)"/><path d="M6 5l2 2-1 1.3c.7 1.3 1.5 2.1 2.7 2.7L11 10l2 2-1.3 1.3C9 13 5 9 4.7 6.3z" fill="#fff"/></svg>
          202-555-0187
        </li>
        <li>
          <svg viewBox="0 0 18 18"><circle cx="9" cy="9" r="9" fill="var(--green)"/><rect x="6.3" y="4" width="5.4" height="10" rx="1" fill="#fff"/><rect x="7.2" y="5.2" width="3.6" height="6.3" fill="var(--green)"/></svg>
          410-555-0163
        </li>
        <li>
          <svg viewBox="0 0 18 18"><circle cx="9" cy="9" r="9" fill="var(--green)"/><rect x="4.5" y="6" width="9" height="6.2" fill="#fff"/><path d="M4.5 6l4.5 3.6L13.5 6" fill="none" stroke="var(--green)" stroke-width="1"/></svg>
          rpdunmore@harborkeys-example.net
        </li>
        <li>
          <svg viewBox="0 0 18 18"><circle cx="9" cy="9" r="9" fill="var(--green)"/><circle cx="9" cy="9" r="4.8" fill="none" stroke="#fff" stroke-width="1.1"/><ellipse cx="9" cy="9" rx="2" ry="4.8" fill="none" stroke="#fff" stroke-width="1"/><path d="M4.2 9h9.6" stroke="#fff" stroke-width="1"/></svg>
          www.harborkeys-example.net
        </li>
      </ul>
    </div>

    <svg class="bands" viewBox="0 0 1000 110" preserveAspectRatio="none" aria-hidden="true">
      <polygon points="0,30 690,30 740,110 0,110" fill="var(--green)"/>
      <polygon points="0,30 690,30 698,43 0,43" fill="var(--green-dark)" opacity=".45"/>
      <polygon points="745,30 1000,30 1000,110 795,110" fill="var(--black-band)"/>
    </svg>
  </div>
</body>
</html>
```